Corvane Capital Business Cards

These are professional business cards that are for my family office.
Put fake emails and phone numbers as of now until I finalize those components. This family office controls my families investments, assets, and future. The cards should be professional.
..
.
.
.
I just uploaded another variation of a logo I would like to see as a business card to I am inbeteen which logo to use

Target Market(s)

business

Industry/Entity Type

business

Contact Information for Business Card

Professional, wealth related, finance related.

Requirements
Must have
• Logo

```html
<!DOCTYPE html>
<html lang="en">
<head>
<meta charset="utf-8">
<title>Corvane Capital Business Cards</title>
<link rel="stylesheet" href="https://fonts.googleapis.com/css2?family=Crimson+Pro:wght@400;600&display=swap">
<style>
  :root {
    --page: #e9e7e3;
    --navy: #1b2234;
    --navy-light: #2c3550;
    --navy-dark: #121725;
    --ink: #1c2233;
    --muted: #5c6170;
    --white: #ffffff;
    --paper-shade: #e6e6e6;
    --rule: #9ea2ad;
    --faint: #dedfe2;
  }
  * { box-sizing: border-box; margin: 0; padding: 0; }
  html, body { width: 1200px; height: 900px; overflow: hidden; }
  body {
    background: var(--page);
    font-family: "Crimson Pro", Georgia, serif;
    position: relative;
  }
  .card {
    position: absolute;
    left: 340px;
    width: 520px;
    height: 300px;
    border-radius: 26px;
    overflow: hidden;
    box-shadow: 0 6px 18px rgba(0,0,0,0.18);
  }
  /* Back side */
  .card-back {
    top: 120px;
    background: radial-gradient(ellipse at 50% 40%, var(--navy-light) 0%, var(--navy) 55%, var(--navy-dark) 100%);
    color: var(--white);
  }
  .back-brand {
    position: absolute;
    top: 78px;
    left: 0;
    right: 0;
    display: flex;
    align-items: center;
    justify-content: center;
    gap: 14px;
  }
  .brand-dot {
    width: 22px;
    height: 22px;
    border: 2px solid var(--white);
    border-radius: 50%;
  }
  .back-brand .brand-name {
    font-size: 30px;
    font-weight: 400;
    letter-spacing: 3px;
    font-variant: small-caps;
    color: var(--white);
  }
  .back-rule {
    position: absolute;
    top: 172px;
    left: 110px;
    right: 110px;
    height: 1px;
    background: linear-gradient(90deg, transparent, rgba(255,255,255,0.45), transparent);
  }
  .back-web {
    position: absolute;
    top: 186px;
    left: 0;
    right: 0;
    text-align: center;
    font-size: 15px;
    letter-spacing: 6px;
    font-weight: 600;
  }
  /* Front side */
  .card-front {
    top: 480px;
    background: linear-gradient(115deg, var(--white) 0%, var(--paper-shade) 45%, var(--white) 100%);
    color: var(--ink);
  }
  .front-accent {
    position: absolute;
    top: 14px;
    right: 28px;
    width: 150px;
    height: 150px;
    border: 2px solid var(--faint);
    border-radius: 50%;
  }
  .front-brand {
    position: absolute;
    top: 56px;
    left: 36px;
    display: flex;
    align-items: center;
    gap: 12px;
  }
  .front-brand .brand-dot { border-color: var(--ink); width: 20px; height: 20px; }
  .front-brand .brand-name {
    font-size: 32px;
    font-weight: 600;
    font-variant: small-caps;
    letter-spacing: 1px;
    color: var(--ink);
  }
  .holder {
    position: absolute;
    left: 120px;
    top: 196px;
    width: 148px;
    text-align: right;
  }
  .holder-title { font-size: 15px; color: var(--muted); }
  .holder-name { font-size: 18px; font-weight: 600; letter-spacing: 0.5px; }
  .divider {
    position: absolute;
    left: 282px;
    top: 168px;
    width: 1px;
    height: 90px;
    background: var(--rule);
  }
  .contact-list {
    position: absolute;
    left: 298px;
    top: 166px;
    list-style: none;
  }
  .contact-list li {
    display: flex;
    align-items: center;
    gap: 8px;
    font-size: 14.5px;
    height: 23px;
    color: var(--ink);
  }
  .contact-list svg { width: 13px; height: 13px; fill: var(--ink); flex: none; }
</style>
</head>
<body>
  <section class="card card-back">
    <div class="back-brand">
      <span class="brand-dot"></span>
      <span class="brand-name">Corvane Capital</span>
    </div>
    <div class="back-rule"></div>
    <p class="back-web">www.corvanecapital.com</p>
  </section>

  <section class="card card-front">
    <div class="front-accent"></div>
    <div class="front-brand">
      <span class="brand-dot"></span>
      <span class="brand-name">Corvane Capital</span>
    </div>
    <div class="holder">
      <p class="holder-title">Director</p>
      <p class="holder-name">ELLIOT MARSH</p>
    </div>
    <div class="divider"></div>
    <ul class="contact-list">
      <li>
        <svg viewBox="0 0 24 24"><path d="M6.6 10.8a15.1 15.1 0 0 0 6.6 6.6l2.2-2.2a1 1 0 0 1 1-.25 11.4 11.4 0 0 0 3.6.57 1 1 0 0 1 1 1V20a1 1 0 0 1-1 1A17 17 0 0 1 3 4a1 1 0 0 1 1-1h3.5a1 1 0 0 1 1 1c0 1.25.2 2.45.57 3.57a1 1 0 0 1-.25 1z"/></svg>
        300-400-7000
      </li>
      <li>
        <svg viewBox="0 0 24 24"><path d="M2 5h20v14H2z M3 6l9 7 9-7" fill="none" stroke="currentColor"/><path d="M2 5h20v2l-10 7L2 7z"/><path d="M2 8l10 7 10-7v11H2z"/></svg>
        info@corvanecapital.com
      </li>
      <li>
        <svg viewBox="0 0 24 24"><path d="M12 2a10 10 0 1 0 0 20 10 10 0 0 0 0-20zm0 2c.9 1.2 1.6 2.8 1.9 5h-3.8c.3-2.2 1-3.8 1.9-5zM9.6 4.4A12 12 0 0 0 8.1 9H4.9a8 8 0 0 1 4.7-4.6zm4.8 0A8 8 0 0 1 19.1 9h-3.2a12 12 0 0 0-1.5-4.6zM4.3 11h3.6a18 18 0 0 0 0 2H4.3a8 8 0 0 1 0-2zm5.7 0h4a16 16 0 0 1 0 2h-4a16 16 0 0 1 0-2zm6.1 0h3.6a8 8 0 0 1 0 2h-3.6a18 18 0 0 0 0-2zM4.9 15h3.2a12 12 0 0 0 1.5 4.6A8 8 0 0 1 4.9 15zm5.2 0h3.8c-.3 2.2-1 3.8-1.9 5-.9-1.2-1.6-2.8-1.9-5zm5.8 0h3.2a8 8 0 0 1-4.7 4.6 12 12 0 0 0 1.5-4.6z"/></svg>
        www.corvanecapital.com
      </li>
      <li>
        <svg viewBox="0 0 24 24"><path d="M12 2a7 7 0 0 0-7 7c0 5 7 13 7 13s7-8 7-13a7 7 0 0 0-7-7zm0 9.5A2.5 2.5 0 1 1 12 6.5a2.5 2.5 0 0 1 0 5z"/></svg>
        00 dummy city, dummy place 0000
      </li>
    </ul>
  </section>
</body>
</html>
```